NEW Wordpress Website Design for a Dynamic Long Term Healthcare Company in Hawaii

I would like a new website design for my current company, Marlow Health Collective, which has two different brands - Marlow Homecare and Marlow Senior Living. You can see the current website at www.marlowhealth-example.com. The website should be built using Wordpress Software and the Framewise theme. The website should have a local Hawaii island/tropical feel, but look professional for healthcare. I'm looking for something fresh, and want the designer to select colors, styles, etc.

In the Header, on all pages, I would like a menu that includes Home Care, Senior Living, Rates, and About Us.
Under each of the Header Menu Titles, I would like these drop downs included:
Home Care (drop down pages)- Nurse Aide Care, 24-Hour Home Care, Skilled Nursing, Lifestyle Aide, Hospice at Home, Bathing & Meal Service.
Senior Living (drop down pages) - Long-Term Stay, Short-Term Stay.
Rates (drop down page) - Rates.
About Us (drop down pages) - Our Mission, Ohana Talk, About Dana Marlow.

In the footer, on all pages, you should include the address: 248 Pueo Lane, Suite 310, Honolulu, HI 96817. Phone number: 808-555-0172
The footer should also include buttons for a page called Learn, Caregiver Jobs, and each of the service page links to include: Nurse Aide Care, 24-Hour Home Care, Skilled Nursing, Lifestyle Aide, Hospice at Home, Bathing & Meal Service.
Please don't take the current website and redesign a few aspects. I'm looking for a completely different look and feel.

Target Market(s)

40-80 year olds

Industry/Entity Type

Long Term Healthcare

Coding

Coded - Design and coding required

Requirements
Should not have
• Our existing website as a template. We are looking for a complete redesign. Thank you.

```html
<!DOCTYPE html>
<html lang="en">
<head>
<meta charset="utf-8">
<title>Marlow Health Collective — Homecare & Senior Living</title>
<link href="https://fonts.googleapis.com/css2?family=Poppins:ital,wght@0,400;0,500;0,600;0,700;1,500&display=swap" rel="stylesheet">
<style>
:root{
  --teal:#5b9a94;
  --teal-dark:#3f7f79;
  --coral:#e9806f;
  --coral-soft:#f3b7aa;
  --ink:#2c2c2c;
  --muted:#6b6b6b;
  --mist:#eef5f4;
  --white:#ffffff;
  --line:#d9e6e4;
}
*{box-sizing:border-box;margin:0;padding:0}
html,body{width:1200px;height:4316px;overflow:hidden}
body{font-family:"Poppins",sans-serif;color:var(--ink);background:var(--white);position:relative}
a{color:inherit;text-decoration:none}
.btn{display:inline-block;background:var(--coral);color:var(--white);font-size:13px;font-weight:600;letter-spacing:.5px;text-transform:uppercase;padding:14px 28px;border-radius:30px}

/* header */
.site-header{height:152px;position:relative;padding:0 60px}
.brand-pair{position:absolute;left:80px;top:42px;display:flex;gap:28px;align-items:center}
.brand{display:flex;align-items:center;gap:8px;font-size:17px;font-weight:600;color:var(--teal)}
.brand .dot{width:16px;height:16px;border-radius:50%;background:var(--coral)}
.brand.coral{color:var(--coral)}
.brand.coral .dot{background:var(--teal)}
.top-contacts{position:absolute;right:70px;top:14px;display:flex;gap:28px;font-size:12px;color:var(--muted)}
.top-contacts span{display:flex;align-items:center;gap:8px}
.top-contacts svg{width:18px;height:18px}
.main-nav{position:absolute;right:70px;top:86px;display:flex;gap:34px;font-size:15px;font-weight:500}
.main-nav a{display:flex;align-items:center;gap:6px}
.main-nav a::after{content:"";width:7px;height:7px;border-right:2px solid var(--ink);border-bottom:2px solid var(--ink);transform:rotate(45deg) translateY(-3px)}
.main-nav a.plain::after{display:none}

/* hero */
.hero{position:relative;height:620px;overflow:hidden}
.hero-photo{position:absolute;inset:0;background:linear-gradient(100deg,#7b6a55 0%,#b49b78 35%,#d9c7a4 60%,#8fa394 100%)}
.hero-shade{position:absolute;inset:0;background:linear-gradient(90deg,rgba(30,30,30,.55) 0%,rgba(30,30,30,.25) 45%,rgba(0,0,0,0) 70%)}
.hero-copy{position:absolute;left:108px;top:70px;width:560px;color:var(--white)}
.hero-copy h1{font-size:40px;line-height:1.2;font-weight:700;letter-spacing:1px;text-transform:uppercase}
.hero-copy p{margin-top:22px;font-size:15px;line-height:1.7}
.hero-copy .btn{margin-top:50px}
.hero-wave{position:absolute;left:0;bottom:0;width:1200px;height:150px}

/* services */
.services{height:720px;padding:30px 0 0}
.section-title{font-size:40px;font-weight:700;color:var(--teal);text-transform:uppercase;letter-spacing:1px}
.services .section-title{padding-left:132px}
.service-grid{display:flex;gap:40px;padding:0 132px;margin-top:50px}
.service-card{width:448px}
.service-photo{height:300px;border-radius:6px}
.photo-homecare{background:linear-gradient(135deg,#e7d67c,#b9a35a 60%,#5f8fa5)}
.photo-living{background:linear-gradient(135deg,#c45b3e,#e6b27a 55%,#7f6a4b)}
.service-card h3{margin-top:28px;font-size:26px;line-height:1.35;font-weight:600}
.service-card p{margin-top:14px;font-size:12px;line-height:1.7;color:var(--muted)}
.service-card .btn{margin-top:38px}

/* care */
.care{height:760px;background:var(--mist);padding-top:60px;text-align:center}
.care .lead{width:560px;margin:18px auto 0;font-size:13px;line-height:1.7;color:var(--muted)}
.care-grid{display:grid;grid-template-columns:repeat(3,228px);gap:40px 24px;justify-content:center;margin-top:36px}
.care-card{height:220px;background:var(--white);border-radius:8px;box-shadow:0 4px 14px rgba(0,0,0,.06);padding:38px 24px;text-align:left}
.care-card svg{width:60px;height:60px}
.care-card h4{margin-top:22px;font-size:14px;font-weight:500;line-height:1.45}

/* consultation */
.consult{height:660px;display:flex}
.consult-photo{width:600px;height:660px;background:linear-gradient(160deg,#3f6b3a 0%,#7fa36a 40%,#c7b38a 75%,#a5814f 100%)}
.consult-panel{width:600px;background:var(--teal);padding:40px 70px 0 76px;color:var(--white)}
.consult-panel h2{font-size:28px;line-height:1.3;font-weight:700;text-transform:uppercase;letter-spacing:.5px}
.consult-form{margin-top:26px;display:flex;flex-direction:column;gap:14px}
.field{height:50px;border-radius:25px;background:var(--white);color:var(--muted);font-size:13px;padding:0 24px;display:flex;align-items:center}
.consult-note{font-size:10px;line-height:1.5;opacity:.9;margin-top:-2px}
.submit{height:48px;border-radius:25px;background:var(--coral);color:var(--white);font-size:13px;font-weight:600;text-transform:uppercase;display:flex;align-items:center;justify-content:center;margin-top:6px}

/* about */
.about{height:600px;position:relative;padding-top:80px}
.about .section-title{text-align:center}
.about-photo{position:absolute;left:160px;top:180px;width:372px;height:440px;border-radius:8px;background:linear-gradient(140deg,#d9c49a,#8a6a45 55%,#3f7fa8)}
.about-copy{position:absolute;left:592px;top:190px;width:548px;font-size:13px;line-height:1.75;color:var(--muted)}
.about-copy p+p{margin-top:22px}
.about .btn{position:absolute;left:592px;top:560px}

/* quote */
.quote{height:380px;text-align:center;padding-top:60px;background:linear-gradient(var(--white),var(--mist))}
.quote-mark{width:44px;height:44px;border-radius:50%;background:var(--teal);margin:0 auto}
.quote blockquote{margin-top:50px;font-size:30px;line-height:1.45;font-style:italic;font-weight:500;color:var(--teal-dark)}

/* footer */
.site-footer{height:416px;position:relative;background:var(--white);border-top:1px solid var(--line)}
.footer-brands{position:absolute;left:160px;top:50px;display:flex;gap:30px}
.footer-brands .brand{font-size:15px;width:130px;flex-wrap:wrap;line-height:1.3}
.footer-contact{position:absolute;left:160px;top:180px;font-size:14px;color:var(--muted);display:flex;flex-direction:column;gap:22px}
.footer-contact span{display:flex;align-items:center;gap:14px}
.footer-contact svg{width:34px;height:34px;flex:none}
.footer-col{position:absolute;top:50px}
.footer-col h5{font-size:14px;font-weight:700;text-transform:uppercase;letter-spacing:.5px}
.footer-col ul{list-style:none;margin-top:18px;font-size:14px;line-height:2.15;color:var(--muted)}
.col-pages{left:644px}
.col-services{left:872px}
.footer-bar{position:absolute;left:160px;right:160px;bottom:0;height:70px;border-top:1px solid var(--line);display:flex;align-items:center;justify-content:space-between;font-size:11px;color:var(--muted)}
.social{display:flex;gap:10px}
.social i{width:26px;height:26px;border-radius:50%;background:var(--teal);display:block}
</style>
</head>
<body>

<header class="site-header">
  <div class="brand-pair">
    <span class="brand"><span class="dot"></span>Marlow Homecare</span>
    <span class="brand coral"><span class="dot"></span>Marlow Senior Living</span>
  </div>
  <div class="top-contacts">
    <span><svg viewBox="0 0 24 24"><circle cx="12" cy="12" r="12" fill="#5b9a94"/><path d="M9 7l2 2-1.2 1.5a7 7 0 0 0 3.7 3.7L15 13l2 2-1.5 1.8C11 16.5 7.5 13 7.2 8.5z" fill="#fff"/></svg>+1 (808) 555-0172</span>
    <span><svg viewBox="0 0 24 24"><circle cx="12" cy="12" r="12" fill="#e9806f"/><path d="M9 7l2 2-1.2 1.5a7 7 0 0 0 3.7 3.7L15 13l2 2-1.5 1.8C11 16.5 7.5 13 7.2 8.5z" fill="#fff"/></svg>+1 (808) 555-0172</span>
  </div>
  <nav class="main-nav">
    <a href="#">Home Care</a>
    <a href="#">Senior Living</a>
    <a href="#" class="plain">Rates</a>
    <a href="#">About Us</a>
  </nav>
</header>

<section class="hero">
  <div class="hero-photo" role="img" aria-label="Photo of a caregiver sitting with an elderly woman in a bright home living room"></div>
  <div class="hero-shade"></div>
  <div class="hero-copy">
    <h1>Hawaii's Choice<br>Homecare &amp; Senior Living</h1>
    <p><strong>Marlow Homecare</strong> provides a variety of professional in-home health care services throughout the entire island of Oahu. <strong>Marlow Senior Living</strong>, a beautiful Adult Residential Care Home, is located on the windward side of Oahu in Kailua.</p>
    <a href="#" class="btn">Learn More</a>
  </div>
  <svg class="hero-wave" viewBox="0 0 1200 150" preserveAspectRatio="none">
    <path d="M0 110 C 300 150, 600 40, 900 40 C 1050 40, 1150 70, 1200 90 L1200 150 L0 150 Z" fill="#ffffff"/>
    <path d="M0 95 C 300 140, 600 20, 900 22 C 1050 24, 1150 55, 1200 78" fill="none" stroke="#5b9a94" stroke-width="14"/>
  </svg>
</section>

<section class="services">
  <h2 class="section-title">Our Services</h2>
  <div class="service-grid">
    <article class="service-card">
      <div class="service-photo photo-homecare" role="img" aria-label="Photo of a nurse caring for an older man at home"></div>
      <h3>Home Care - Professional Care In Your Home</h3>
      <p>Marlow Homecare understands that every person's care journey is unique. We tailor our in-home services to meet the diverse nurturing experience of professional quality care and safety within the comfort and convenience of your own home.</p>
      <a href="#" class="btn">Schedule Care Assessment</a>
    </article>
    <article class="service-card">
      <div class="service-photo photo-living" role="img" aria-label="Photo of residents sharing a meal at a senior living home"></div>
      <h3>Senior Living - Trusted Care In Our Home</h3>
      <p>Marlow Homecare understands that every person's care journey is unique. We tailor our in-home services to meet the diverse nurturing experience of professional quality care and safety within the comfort and convenience of your own home.</p>
      <a href="#" class="btn">Schedule Tour</a>
    </article>
  </div>
</section>

<section class="care">
  <h2 class="section-title" style="color:var(--coral)">We Care Always</h2>
  <p class="lead">Lorem ipsum dolor sit amet, consectetur adipiscing elit, sed do eiusmod tempor incididunt ut labore et dolore magna aliqua.</p>
  <div class="care-grid">
    <div class="care-card">
      <svg viewBox="0 0 60 60"><rect x="6" y="10" width="48" height="44" rx="8" fill="#f3b7aa"/><circle cx="30" cy="26" r="9" fill="#5b9a94"/><rect x="16" y="38" width="28" height="12" rx="6" fill="#5b9a94"/></svg>
      <h4>Skilled Nurses &amp;<br>Caregivers</h4>
    </div>
    <div class="care-card">
      <svg viewBox="0 0 60 60"><rect x="12" y="8" width="36" height="46" rx="6" fill="#f3b7aa"/><rect x="26" y="20" width="8" height="24" fill="#5b9a94"/><rect x="18" y="28" width="24" height="8" fill="#5b9a94"/></svg>
      <h4>Medication<br>Services</h4>
    </div>
    <div class="care-card">
      <svg viewBox="0 0 60 60"><rect x="6" y="30" width="48" height="16" rx="6" fill="#5b9a94"/><rect x="10" y="10" width="6" height="22" rx="3" fill="#e9806f"/><rect x="14" y="46" width="6" height="8" fill="#e9806f"/><rect x="40" y="46" width="6" height="8" fill="#e9806f"/></svg>
      <h4>Bathing/Showering<br>Dressing &amp; Grooming</h4>
    </div>
    <div class="care-card">
      <svg viewBox="0 0 60 60"><rect x="6" y="10" width="48" height="44" rx="8" fill="#f3b7aa"/><circle cx="30" cy="26" r="9" fill="#5b9a94"/><rect x="16" y="38" width="28" height="12" rx="6" fill="#5b9a94"/></svg>
      <h4>Skilled Nurses &amp;<br>Caregivers</h4>
    </div>
    <div class="care-card">
      <svg viewBox="0 0 60 60"><rect x="12" y="8" width="36" height="46" rx="6" fill="#f3b7aa"/><rect x="26" y="20" width="8" height="24" fill="#5b9a94"/><rect x="18" y="28" width="24" height="8" fill="#5b9a94"/></svg>
      <h4>Medication<br>Services</h4>
    </div>
    <div class="care-card">
      <svg viewBox="0 0 60 60"><rect x="6" y="30" width="48" height="16" rx="6" fill="#5b9a94"/><rect x="10" y="10" width="6" height="22" rx="3" fill="#e9806f"/><rect x="14" y="46" width="6" height="8" fill="#e9806f"/><rect x="40" y="46" width="6" height="8" fill="#e9806f"/></svg>
      <h4>Bathing/Showering<br>Dressing &amp; Grooming</h4>
    </div>
  </div>
</section>

<section class="consult">
  <div class="consult-photo" role="img" aria-label="Photo of a caregiver helping an older woman walk with a walker in a tropical garden"></div>
  <div class="consult-panel">
    <h2>Schedule a Complimentary Care Consultation</h2>
    <div class="consult-form">
      <div class="field">Name *</div>
      <div class="field">Email *</div>
      <div class="field">Phone *</div>
      <div class="field">How can we help you?</div>
      <div class="field">Questions/Comments</div>
      <div class="field">May we email you about this?</div>
      <p class="consult-note"><strong>Note:</strong> You agree to receive care updates and reminders by email from our team.</p>
      <div class="submit">Submit</div>
    </div>
  </div>
</section>

<section class="about">
  <h2 class="section-title">About Us</h2>
  <div class="about-photo" role="img" aria-label="Photo of two caregivers smiling together on a sofa"></div>
  <div class="about-copy">
    <p>At Marlow Health Collective, our mission is to provide compassionate and professional long-term healthcare services that empower individuals to maintain their highest level of independence, health, and well-being in the comfort of their own homes or ours, either through our licensed home healthcare agency – Marlow Homecare, or in our Adult Residential Care Home – Marlow Senior Living.</p>
    <p>We are dedicated to delivering personalized care that addresses the unique needs of each client, fostering a sense of trust, respect and dignity. Our team of skilled healthcare professionals is committed to creating a supportive environment that not only attends to medical needs but also promotes emotional and social well-being.</p>
  </div>
  <a href="#" class="btn">Learn More</a>
</section>

<section class="quote">
  <div class="quote-mark"></div>
  <blockquote>“Caregiving is a series of small acts of care that<br>alter the course of someone's life”</blockquote>
</section>

<footer class="site-footer">
  <div class="footer-brands">
    <span class="brand"><span class="dot"></span>Marlow Health Collective</span>
    <span class="brand"><span class="dot"></span>Marlow Homecare</span>
    <span class="brand coral"><span class="dot"></span>Marlow Senior Living</span>
  </div>
  <div class="footer-contact">
    <span><svg viewBox="0 0 34 34"><circle cx="17" cy="17" r="17" fill="#eef5f4"/><path d="M17 9a6 6 0 0 1 6 6c0 4.5-6 10-6 10s-6-5.5-6-10a6 6 0 0 1 6-6z" fill="#5b9a94"/><circle cx="17" cy="15" r="2.2" fill="#fff"/></svg>248 Pueo Lane, Suite 310,<br>Honolulu, HI 96817</span>
    <span><svg viewBox="0 0 34 34"><circle cx="17" cy="17" r="17" fill="#eef5f4"/><path d="M13 10l3 3-1.6 2a9 9 0 0 0 5 5l2-1.6 3 3-2 2.4C16 23.5 11 18.5 10.6 12.2z" fill="#5b9a94"/></svg>(808) 555-0172</span>
  </div>
  <div class="footer-col col-pages">
    <h5>Pages</h5>
    <ul><li>Home</li><li>About Us</li><li>Learn</li><li>Caregiver Jobs</li></ul>
  </div>
  <div class="footer-col col-services">
    <h5>Services</h5>
    <ul><li>Nurse Aide Care</li><li>24 Hour Home Care</li><li>Skilled Nursing</li><li>Lifestyle Aide</li><li>Hospice at Home</li><li>Bathing &amp; Meal Service</li></ul>
  </div>
  <div class="footer-bar">
    <span>© 2023 Marlow Health Collective. All Rights Reserved.</span>
    <div class="social"><i></i><i></i><i></i><i></i></div>
  </div>
</footer>

</body>
</html>
```